Keystonery Billboard - Financial Services Company (Investments, Tax Planning and Insurance)

Our new office has a billboard directly above the office building. We'd like something eye-catching with a strong Call to Action, with the main part of the billboard being under 7 words if possible. We'd like you to include a way to get ahold of us (either our website keystoneryllc.example or our phone number 302-418-2907. You may also include in small font something to indicate that we've been serving the area since 1980 (the DE area, the tri-state area, the Marlowe Hollow, etc.)

We offer financial planning, tax planning, and insurance, and we help our clients to focus on their goals and happiness by providing everything they need for lifelong wealth under one roof.

Our logos are attached, we use a triangle logo with green and gray. We use the tagline "discover lasting prosperity" but this does not need to be included.

Potential ideas we have seen from other financial companies-
- the concept that the driver spends more time looking at billboards than planning for their retirement
-something along the lines of "everything you need for your finances is in this building right here" planning, investments, taxes, insurance"
-don't spend your time worrying about retirement, let us help you plan for it
-are you working for your money, or is it working for you?
- retirement takes planning, we're here to help
- ready to retire? talk to us
- need investment advice?
- need help investing?
- crossing your fingers isn't a retirement plan. we can help.
- retiring soon? you need help.

Those are just general ideas, please feel free to be creative.

brand colors:
#00b585
#00b185
#000000
#ffffff
#6d6f75
#6d6f75
#6f7074
#021712
#052e24

```html
<!DOCTYPE html>
<html lang="en">
<head>
<meta charset="utf-8">
<title>Keystonery Billboard</title>
<link rel="stylesheet" href="https://fonts.googleapis.com/css2?family=Bebas+Neue&family=Poppins:wght@500;600;700&display=swap">
<style>
  :root {
    --brand-green: #12954f;
    --brand-green-deep: #0c7f42;
    --ink: #1f1f1f;
    --paper: #ffffff;
    --band-dark: #222222;
    --photo-warm: #d9c7a8;
    --photo-cool: #c9cdd2;
  }
  * { margin: 0; padding: 0; box-sizing: border-box; }
  html, body { width: 1112px; height: 1200px; overflow: hidden; background: var(--paper); }
  .billboard {
    position: absolute; left: 36px; top: 448px;
    width: 1040px; height: 303px;
    background: linear-gradient(135deg, var(--brand-green), var(--brand-green-deep));
    box-shadow: 0 6px 22px rgba(0,0,0,.35);
    overflow: hidden;
  }
  .billboard__shapes { position: absolute; inset: 0; }
  .headline {
    position: absolute; left: 31px; top: 26px; height: 91px;
    display: flex; align-items: center;
    font-family: "Bebas Neue", sans-serif; font-size: 78px; line-height: 1;
    color: var(--paper); letter-spacing: 0.2px; padding-top: 6px;
  }
  .services {
    position: absolute; left: 31px; top: 142px;
    display: flex; align-items: center; gap: 22px;
    font-family: "Poppins", sans-serif; font-weight: 500; font-size: 22px;
    color: var(--paper);
  }
  .service { display: flex; align-items: center; gap: 10px; }
  .service__icon { width: 36px; height: 36px; }
  .contact {
    position: absolute; left: 31px; top: 214px; height: 89px;
    display: flex; align-items: center; gap: 48px;
  }
  .brand-name {
    font-family: "Poppins", sans-serif; font-weight: 600; font-size: 32px;
    color: var(--brand-green);
  }
  .phone {
    font-family: "Poppins", sans-serif; font-weight: 700; font-size: 50px;
    color: var(--ink); letter-spacing: 0.5px;
  }
</style>
</head>
<body>
  <section class="billboard">
    <svg class="billboard__shapes" width="1040" height="303" viewBox="0 0 1040 303">
      <polygon class="headline-band" points="0,26 712,26 699,117 0,117" fill="var(--band-dark)"/>
      <polygon class="contact-band" points="0,214 690,214 678,303 0,303" fill="var(--paper)"/>
      <polygon class="photo-frame" points="726,0 1038,0 990,303 663,303" fill="var(--paper)"/>
      <polygon class="photo-area" role="img" aria-label="Photo of a smiling older couple reviewing finances at a laptop with a piggy bank" points="735,0 1029,0 981,303 672,303" fill="url(#photoTone)"/>
      <defs>
        <linearGradient id="photoTone" x1="0" y1="0" x2="1" y2="1">
          <stop offset="0" stop-color="var(--photo-warm)"/>
          <stop offset="1" stop-color="var(--photo-cool)"/>
        </linearGradient>
      </defs>
    </svg>

    <h1 class="headline">NEED INVESTMENT ADVICE?</h1>

    <ul class="services">
      <li class="service">
        <svg class="service__icon" viewBox="0 0 36 36" aria-hidden="true">
          <circle cx="18" cy="18" r="16" fill="var(--band-dark)" stroke="var(--paper)" stroke-width="1.5"/>
          <rect x="11" y="11" width="14" height="14" rx="1.5" fill="none" stroke="var(--paper)" stroke-width="1.5"/>
          <line x1="14" y1="16" x2="22" y2="16" stroke="var(--paper)" stroke-width="1.5"/>
          <line x1="14" y1="20" x2="20" y2="20" stroke="var(--paper)" stroke-width="1.5"/>
        </svg>
        <span>Financial planning</span>
      </li>
      <li class="service">
        <svg class="service__icon" viewBox="0 0 36 36" aria-hidden="true">
          <circle cx="18" cy="18" r="16" fill="var(--band-dark)" stroke="var(--paper)" stroke-width="1.5"/>
          <rect x="12" y="10" width="12" height="16" rx="1.5" fill="none" stroke="var(--paper)" stroke-width="1.5"/>
          <rect x="15" y="17" width="2" height="6" fill="var(--paper)"/>
          <rect x="19" y="14" width="2" height="9" fill="var(--paper)"/>
        </svg>
        <span>Tax planning</span>
      </li>
      <li class="service">
        <svg class="service__icon" viewBox="0 0 36 36" aria-hidden="true">
          <circle cx="18" cy="18" r="16" fill="var(--band-dark)" stroke="var(--paper)" stroke-width="1.5"/>
          <path d="M18 9 L25 12 V17 C25 22 22 25 18 27 C14 25 11 22 11 17 V12 Z" fill="none" stroke="var(--paper)" stroke-width="1.5"/>
          <path d="M15 18 L17.5 20.5 L21.5 15.5" fill="none" stroke="var(--paper)" stroke-width="1.5"/>
        </svg>
        <span>Insurance</span>
      </li>
    </ul>

    <div class="contact">
      <span class="brand-name">Keystonery</span>
      <span class="phone">302-418-2907</span>
    </div>
  </section>
</body>
</html>
```